Real estate broker business card

Want a modern celan but effective business card for my residential and commercial real estate business. I want the back of the card to advertise my services and to capture business. I have attached the back of my current business card fore ideas
Updates

Logos, photo and text updates added! Added Saturday, September 3, 2016

Project Deadline Extended Reason: LOGOS, PHOTOS AND TEST JUST UPLOADED! I'M READY TO PICK A DESIGN! THANK YOU! Added Saturday, September 3, 2016

Target Market(s)

home buyers and seller. commercial buyers and sellers

Industry/Entity Type

Real Estate

Contact Information for Business Card

must have my contact information and my photo

Requirements
Must have
• Carla Ventrino
• Owner & Qualifying Broker
• Ventrino Real Estate Services
• 505.718.2094
• carla@ventrinohomes.example
• www.ventrinohomes.example
Nice to have
• metallic
• Business capture text: " Don't buy or lease property without someone looking out for your best interests. I will represent you on your home or investment purchase for FREE!"
• "Home owners, call today to receive a FREE market analysis for your homes value!

```html
<!DOCTYPE html>
<html lang="en">
<head>
<meta charset="utf-8">
<title>Ventrino Real Estate Services – Business Card</title>
<link rel="stylesheet" href="https://fonts.googleapis.com/css2?family=Open+Sans:wght@400;600;700&display=swap">
<style>
  :root {
    --canvas: #eceae8;
    --card-light-top: #ffffff;
    --card-light-bottom: #e4e2e2;
    --teal-top: #22909f;
    --teal-bottom: #0d6676;
    --brand-teal: #1b7f8e;
    --text-light: #ffffff;
    --faint: #c9cccd;
    --shadow: rgba(0, 0, 0, 0.22);
  }
  * { box-sizing: border-box; margin: 0; padding: 0; }
  html, body {
    width: 1200px; height: 900px; overflow: hidden;
    background: var(--canvas);
    font-family: "Open Sans", Arial, sans-serif;
  }
  .stage { position: relative; width: 1200px; height: 900px; }

  .card {
    position: absolute;
    width: 556px; height: 343px;
    overflow: hidden;
    background: linear-gradient(180deg, var(--card-light-top), var(--card-light-bottom));
    box-shadow: 0 6px 18px var(--shadow);
  }
  .card--front { left: 238px; top: 62px; }
  .card--back { left: 459px; top: 518px; width: 560px; }

  .teal-band {
    position: absolute; left: 0; right: 0; bottom: 0;
    background: linear-gradient(180deg, var(--teal-top), var(--teal-bottom));
  }
  .card--front .teal-band { top: 123px; }
  .card--back .teal-band { top: 124px; }

  .portrait { position: absolute; top: 0; height: 343px; }
  .card--front .portrait { right: 0; width: 556px; left: 0; }
  .card--back .portrait { left: 0; width: 560px; }

  .brand {
    position: absolute; display: flex; align-items: center; gap: 10px;
    color: var(--brand-teal); font-weight: 700; line-height: 1.05;
  }
  .brand-square {
    width: 40px; height: 40px; background: var(--brand-teal); flex: none;
  }
  .brand-name { font-size: 24px; letter-spacing: 1px; }
  .brand-sub { font-size: 11px; letter-spacing: 2.6px; }
  .card--front .brand { left: 32px; top: 34px; }

  .contact { position: absolute; left: 25px; top: 150px; color: var(--text-light); }
  .contact-name { font-size: 18px; font-weight: 600; line-height: 1.2; }
  .contact-title { font-size: 13px; font-weight: 400; margin-top: 1px; }
  .company { font-size: 16px; font-weight: 700; margin-top: 27px; }
  .details { list-style: none; margin-top: 12px; font-size: 14px; }
  .details li { display: flex; align-items: center; gap: 8px; height: 20.5px; }
  .details svg { width: 12px; height: 12px; fill: var(--text-light); flex: none; }

  .faint-brand {
    position: absolute; right: 40px; top: 46px;
    color: var(--faint); font-weight: 700; font-size: 26px; letter-spacing: 1px;
  }
  .back-brand {
    position: absolute; left: 345px; top: 150px; width: 200px;
    display: flex; flex-direction: column; align-items: center; gap: 14px;
    color: var(--text-light); font-weight: 700; text-align: center;
  }
  .back-brand .brand-square { width: 60px; height: 60px; background: var(--text-light); opacity: 0.85; }
  .back-brand .brand-name { font-size: 30px; }
  .back-brand .brand-sub { font-size: 11px; letter-spacing: 2.4px; }
</style>
</head>
<body>
<main class="stage">

  <section class="card card--front">
    <div class="teal-band"></div>
    <div class="brand">
      <span class="brand-square"></span>
      <div>
        <div class="brand-name">VENTRINO</div>
        <div class="brand-sub">REAL ESTATE SERVICES</div>
      </div>
    </div>
    <svg class="portrait" viewBox="0 0 556 343" role="img" aria-label="Portrait photo of Carla Ventrino, smiling, dark wavy hair, white lace top">
      <defs>
        <linearGradient id="portraitFront" x1="0" y1="0" x2="0" y2="1">
          <stop offset="0" stop-color="#33231d"/>
          <stop offset="0.45" stop-color="#b98a74"/>
          <stop offset="0.75" stop-color="#e8e4e2"/>
          <stop offset="1" stop-color="#d9d7d6"/>
        </linearGradient>
      </defs>
      <path fill="url(#portraitFront)" d="M556 18 L556 343 L350 343 C360 300 330 280 328 230 C325 150 360 40 440 20 C490 10 540 14 556 18 Z"/>
    </svg>
    <div class="contact">
      <div class="contact-name">Carla Ventrino</div>
      <div class="contact-title">Owner &amp; Qualifying Broker</div>
      <div class="company">Ventrino Real Estate Services</div>
      <ul class="details">
        <li><svg viewBox="0 0 24 24"><path d="M6.6 10.8a15 15 0 0 0 6.6 6.6l2.2-2.2a1 1 0 0 1 1-.25 11.4 11.4 0 0 0 3.6.57 1 1 0 0 1 1 1V20a1 1 0 0 1-1 1A17 17 0 0 1 3 4a1 1 0 0 1 1-1h3.5a1 1 0 0 1 1 1c0 1.25.2 2.45.57 3.57a1 1 0 0 1-.25 1z"/></svg>505.718.2094</li>
        <li><svg viewBox="0 0 24 24"><path d="M2 5h20v14H2z M2 5l10 8 10-8" fill="none" stroke="#fff" stroke-width="0"/><path d="M2 6l10 7 10-7v13H2z"/><path d="M2 4h20l-10 7z"/></svg>carla@ventrinohomes.example</li>
        <li><svg viewBox="0 0 24 24"><circle cx="12" cy="12" r="10"/></svg>www.ventrinohomes.example</li>
      </ul>
    </div>
  </section>

  <section class="card card--back">
    <div class="teal-band"></div>
    <div class="faint-brand">VENTRINO</div>
    <svg class="portrait" viewBox="0 0 560 343" role="img" aria-label="Portrait photo of Carla Ventrino, smiling, dark wavy hair, white lace top">
      <defs>
        <linearGradient id="portraitBack" x1="0" y1="0" x2="0" y2="1">
          <stop offset="0" stop-color="#33231d"/>
          <stop offset="0.45" stop-color="#b98a74"/>
          <stop offset="0.75" stop-color="#e8e4e2"/>
          <stop offset="1" stop-color="#d9d7d6"/>
        </linearGradient>
      </defs>
      <path fill="url(#portraitBack)" d="M0 40 C40 15 140 10 185 50 C230 100 225 200 232 230 L205 343 L0 343 Z"/>
    </svg>
    <div class="back-brand">
      <span class="brand-square"></span>
      <div>
        <div class="brand-name">VENTRINO</div>
        <div class="brand-sub">REAL ESTATE SERVICES</div>
      </div>
    </div>
  </section>

</main>
</body>
</html>
```